Luxury Wine Label for New Startup Winery

We need a wine label for our new winery startup. We have worked with a local designer but do not feel the resulting label / logo have the elevation required to present our brand as a luxury wine. Our winery is called "Quailbrook Vineyards" and we are focused on extremely high quality hand crafted artisan and estate wines from the Pacific Northwest.
We would like to see designs that utilize a tree line, or other imagery that represents the "Quailbrook" part of our company name. Another interesting feature could be wood grain.
A logo will be required based on your design so please design with this in mind:
This logo should be consistent with the wine bottle label design, and should be representative of our high end exclusive wine while giving a sense of place (Oregon/ Pacific Northwest.)
I will supply an image of the design we received from our local designer, PLEASE NOTE: in general we do like wood grain and tree line concepts but feel the execution was poorly done.
ATTN: Logo design should be suitable for use on: Bottles (Red wine/rose/white wine), Bussiness cards, vehicle signage, business signage, etc
P.S.:
If you have a design that is not outside the box we are still interested in seeing it.
Label is for a burgundy style bottle with a label height of 3.5 - 4" and a width of 3.5-4"
any label <= 4"x4" and >=3.5"x3.5" will be acceptable:
HOWEVER Width should be greater than or equal to height due to the bottle format
Target Market(s)
Wine enthusiasts with adequate discretionary budgets to afford $100 bottles of wine.
Industry/Entity Type
Wine / Winery
Requirements
Must have
- A sense of luxury, a feel of exclusivity, and a theme consistent with our product and brand name
Nice to have
- Tree line, wood grain or other wood themes. Serif fonts
Should not have
- anything cheesy, off topic, hard to read script fonts or anything that makes the label hard to read from a few feet away or too busy

```html
<!DOCTYPE html>
<html lang="en">
<head>
<meta charset="utf-8">
<title>Quailbrook Vineyards — Syrah 2024 Label</title>
<link rel="stylesheet" href="https://fonts.googleapis.com/css2?family=Cinzel:wght@600;700&family=Cormorant+Garamond:wght@600&display=swap">
<style>
  :root {
    --backdrop: #f4f2ef;
    --label-paper: #fdfcfa;
    --ink: #2b2220;
    --ink-soft: #5a4a44;
    --wood-dark: #7a4a30;
    --wood-mid: #b07a5a;
    --wood-light: #ead8c8;
    --edge: #e4ded8;
  }
  * { margin: 0; padding: 0; box-sizing: border-box; }
  html, body {
    width: 841px;
    height: 1200px;
    overflow: hidden;
    background: var(--backdrop);
  }
  .canvas {
    position: relative;
    width: 841px;
    height: 1200px;
    display: flex;
    align-items: center;
    justify-content: center;
  }
  .wine-label {
    position: relative;
    width: 720px;
    height: 780px;
    background: var(--label-paper);
    border: 1px solid var(--edge);
    display: flex;
    flex-direction: column;
    align-items: center;
  }
  .brand-mark {
    margin-top: 46px;
    width: 26px;
    height: 26px;
    border: 3px solid var(--ink);
    border-radius: 50%;
  }
  .brand-name {
    margin-top: 22px;
    text-align: center;
    font-family: "Cinzel", "Times New Roman", serif;
    font-weight: 700;
    color: var(--ink);
    line-height: 1;
  }
  .brand-name__primary {
    display: block;
    font-size: 64px;
    letter-spacing: 3px;
  }
  .brand-name__secondary {
    display: block;
    margin-top: 12px;
    font-size: 40px;
    letter-spacing: 4px;
  }
  .wood-band {
    position: absolute;
    left: 0;
    top: 278px;
    width: 720px;
    height: 330px;
  }
  .wine-details {
    position: absolute;
    right: 150px;
    top: 636px;
    text-align: center;
    color: var(--ink);
  }
  .wine-details__varietal {
    font-family: "Cinzel", "Times New Roman", serif;
    font-weight: 600;
    font-size: 34px;
    letter-spacing: 3px;
    line-height: 1;
  }
  .wine-details__region {
    margin-top: 12px;
    font-family: "Cormorant Garamond", "Times New Roman", serif;
    font-weight: 600;
    font-size: 17px;
    letter-spacing: 3px;
    color: var(--ink-soft);
  }
</style>
</head>
<body>
  <main class="canvas">
    <section class="wine-label">
      <div class="brand-mark" aria-hidden="true"></div>
      <h1 class="brand-name">
        <span class="brand-name__primary">QUAILBROOK</span>
        <span class="brand-name__secondary">VINEYARDS</span>
      </h1>

      <svg class="wood-band" viewBox="0 0 720 330" role="img" aria-label="Flowing wood grain illustration in warm brown tones">
        <defs>
          <linearGradient id="woodTone" x1="0" y1="0" x2="1" y2="1">
            <stop offset="0" stop-color="var(--wood-mid)"/>
            <stop offset="0.35" stop-color="var(--wood-dark)"/>
            <stop offset="0.6" stop-color="var(--wood-light)"/>
            <stop offset="1" stop-color="var(--wood-mid)"/>
          </linearGradient>
        </defs>
        <path d="M0 70 C 140 20, 260 40, 400 60 C 520 78, 620 10, 720 0
                 L 720 200 C 620 240, 520 250, 420 270 C 300 300, 150 330, 0 300 Z"
              fill="url(#woodTone)"/>
      </svg>

      <div class="wine-details">
        <p class="wine-details__varietal">SYRAH 2024</p>
        <p class="wine-details__region">WILLAMETTE VALLEY</p>
      </div>
    </section>
  </main>
</body>
</html>
```